Business Card Design Project

- makeup artist business card

- original and creative

- Elegant design

- Feel free to come out with cool designs but stick to being elegant and attractive

- Design relates to makeup

- includes name, occupation, contact numbers, email, website

- regular size business card

- round corner card

- double sided

- on 1 side it should just have the website name in the center " moonveilstudio.net "

Industry/Entity Type

Business

Requirements
Must have
• Delia Marsh
Makeup Artist
USA: +1 (415)772-0461
Singapore: +65 82307915
deliamarsh@moonveilstudio.net
www.moonveilstudio.net
Should not have
• nothing cartoon looking.
Pictures of makeup being grab from the internet.. Examples: eyes or lips.

```html
<!DOCTYPE html>
<html lang="en">
<head>
<meta charset="utf-8">
<title>Delia Marsh — Makeup Artist Business Card</title>
<link rel="stylesheet" href="https://fonts.googleapis.com/css2?family=Parisienne&family=Dawning+of+a+New+Day&family=Arimo:wght@400&display=swap">
<style>
  :root {
    --canvas: #f2f2f2;
    --card-dark: #161616;
    --card-light: #f6f5f3;
    --ink: #141414;
    --ink-light: #f4f4f4;
    --blush: #e9a3b8;
    --rose: #c98aa4;
    --plum: #6c5560;
    --charcoal: #4a4448;
    --sky: #b9dde8;
    --shadow: rgba(0, 0, 0, 0.18);
  }
  * { box-sizing: border-box; margin: 0; padding: 0; }
  html, body {
    width: 1200px;
    height: 1200px;
    overflow: hidden;
    background: var(--canvas);
  }
  .canvas {
    position: relative;
    width: 1200px;
    height: 1200px;
  }
  .card {
    position: absolute;
    left: 250px;
    width: 700px;
    height: 400px;
    border-radius: 22px;
    overflow: hidden;
    box-shadow: 0 12px 30px var(--shadow);
  }
  /* Back side */
  .card--back {
    top: 130px;
    background: var(--card-dark);
    display: flex;
    align-items: center;
    justify-content: center;
  }
  .card--back .site-mark {
    font-family: "Dawning of a New Day", cursive;
    font-size: 64px;
    color: var(--ink-light);
    letter-spacing: 1px;
  }
  /* Front side */
  .card--front {
    top: 630px;
    background: var(--card-light);
  }
  .portrait-art {
    position: absolute;
    left: 0;
    top: 0;
    width: 300px;
    height: 400px;
    background:
      radial-gradient(ellipse 120px 90px at 70px 80px, rgba(233, 163, 184, 0.75), transparent 70%),
      radial-gradient(ellipse 90px 80px at 230px 330px, rgba(185, 221, 232, 0.9), transparent 70%),
      radial-gradient(ellipse 140px 220px at 120px 270px, rgba(74, 68, 72, 0.85), transparent 75%),
      radial-gradient(ellipse 90px 140px at 40px 330px, rgba(201, 138, 164, 0.8), transparent 70%),
      linear-gradient(90deg, rgba(108, 85, 96, 0.35), rgba(246, 245, 243, 0) 100%);
  }
  .identity {
    position: absolute;
    right: 70px;
    top: 92px;
    text-align: right;
  }
  .identity .name {
    font-family: "Parisienne", cursive;
    font-size: 66px;
    line-height: 1;
    color: var(--ink);
  }
  .identity .role {
    font-family: "Arimo", sans-serif;
    font-size: 19px;
    letter-spacing: 1px;
    color: var(--ink);
    margin-top: 4px;
  }
  .contact {
    position: absolute;
    right: 44px;
    bottom: 34px;
    list-style: none;
    text-align: right;
    font-family: "Arimo", sans-serif;
    font-size: 19px;
    line-height: 1.3;
    color: var(--ink);
  }
</style>
</head>
<body>
  <main class="canvas">
    <section class="card card--back" aria-label="Business card, back">
      <p class="site-mark">moonveilstudio.net</p>
    </section>

    <section class="card card--front" aria-label="Business card, front">
      <div class="portrait-art" role="img" aria-label="Watercolour-style illustration of a woman with long flowing hair in pink, blue and charcoal tones"></div>
      <div class="identity">
        <h1 class="name">Delia Marsh</h1>
        <p class="role">MAKEUP ARTIST</p>
      </div>
      <ul class="contact">
        <li>USA: +1 (415)772-0461</li>
        <li>Singapore: +65 82307915</li>
        <li>deliamarsh@moonveilstudio.net</li>
        <li>www.moonveilstudio.net</li>
      </ul>
    </section>
  </main>
</body>
</html>
```